Harrow lawns and yards

Lawn Maintenance, Spring Fall Clean Ups, Stone Walls & Walkways, Commercial and Residental Snow Removal carpentry and handyman services

Industry/Entity Type

Carpentry

Contact Information for Business Card

Harrow Lawns and Yards 83 Pebble Marsh Rd Alderbrook NY 10482 555 261 3087 Cell 555319 5402

```html
<!DOCTYPE html>
<html lang="en">
<head>
<meta charset="utf-8">
<title>Harrow Lawns and Yards – Business Card</title>
<link href="https://fonts.googleapis.com/css2?family=Exo+2:wght@600;700&display=swap" rel="stylesheet">
<style>
  :root {
    --bg: #ecebe6;
    --card: #ffffff;
    --green: #3fae49;
    --green-dark: #2e9a3e;
    --green-light: #9bd94a;
    --band-top: #c8ec7a;
  }
  html, body {
    margin: 0;
    width: 1200px;
    height: 885px;
    overflow: hidden;
    background: var(--bg);
  }
  .canvas {
    width: 1200px;
    height: 885px;
    display: flex;
    align-items: center;
    justify-content: center;
  }
  .card {
    position: relative;
    width: 450px;
    height: 788px;
    background: var(--card);
    box-shadow: 0 10px 30px rgba(0,0,0,0.15);
    font-family: "Exo 2", sans-serif;
    color: var(--green);
    text-align: center;
    overflow: hidden;
  }
  .brand {
    margin-top: 92px;
    display: flex;
    flex-direction: column;
    align-items: center;
    font-weight: 700;
    color: var(--green);
  }
  .brand-mark {
    width: 34px;
    height: 34px;
    border-radius: 50%;
    background: var(--green);
    margin-bottom: 14px;
  }
  .brand-name {
    font-size: 74px;
    line-height: 1;
    letter-spacing: 1px;
  }
  .brand-tag {
    font-size: 27px;
    line-height: 1.2;
    margin-top: 4px;
  }
  .services {
    list-style: none;
    margin: 52px 0 0;
    padding: 0;
    font-weight: 700;
    font-size: 23px;
    line-height: 1.3;
  }
  .contact {
    margin-top: 52px;
    font-weight: 600;
    font-size: 24px;
    line-height: 1.3;
  }
  .phone {
    display: flex;
    align-items: center;
    justify-content: center;
    gap: 10px;
  }
  .phone svg { width: 18px; height: 18px; }
  .address { margin-top: 6px; }
  .band {
    position: absolute;
    left: 0; right: 0; bottom: 0;
    height: 112px;
    background: linear-gradient(to bottom, #ffffff 0%, var(--band-top) 35%, var(--green-light) 70%, var(--green-dark) 100%);
  }
</style>
</head>
<body>
<div class="canvas">
  <div class="card">
    <div class="brand">
      <div class="brand-mark"></div>
      <div class="brand-name">Harrow</div>
      <div class="brand-tag">Lawns and Yards</div>
    </div>

    <ul class="services">
      <li>Lawn Maintenance</li>
      <li>Spring Fall Clean Ups</li>
      <li>Stone Walls &amp; Walkways</li>
      <li>Commercial and Residental</li>
      <li>Snow Removal carpentry and</li>
      <li>handyman services</li>
    </ul>

    <div class="contact">
      <div class="phone">
        <svg viewBox="0 0 18 18" aria-hidden="true"><rect width="18" height="18" rx="2" fill="var(--green)"/><rect x="6" y="3" width="6" height="12" rx="1" fill="#fff"/><rect x="7" y="4.5" width="4" height="4" fill="var(--green)"/></svg>
        <span>555319 5402</span>
      </div>
      <div class="phone">
        <svg viewBox="0 0 18 18" aria-hidden="true"><rect width="18" height="18" rx="2" fill="var(--green)"/><path d="M4 8 Q9 3 14 8 L12 9 Q9 7 6 9 Z" fill="#fff"/><rect x="5" y="10" width="8" height="4" rx="1" fill="#fff"/></svg>
        <span>555 261 3087</span>
      </div>
      <div class="address">83 Pebble Marsh Rd Alderbrook<br>NY 10482</div>
    </div>

    <div class="band"></div>
  </div>
</div>
</body>
</html>
```